Coffee House With Cycling Theme Wants Business Cards

We want to create a business card for a coffee house that has a cycling theme. We expect to use the current logo on one side of the business card and we have been considering adding the words 'COFFEE HOUSE' underneath (see example). For the other side of the business card we want an interesting design with tag-line, address and social media links (the normal business card stuff). See examples provided but we are not fixed on having it exactly as shown, we are very open to great creative ideas. Please note our logo has the initials ‘KR' in orange embedded in the design and this must be retained. However, you can play with the words COFFEE HOUSE as well as use the orange color on the backside of the business card, as you see fit. For an image on the backside of the business card it can be a photo, hand-drawn or whatever but it must visually combine coffee and cycling in some way. The interior of the Coffee House will be reclaimed wood, rustic and have an urban feel to it with cycling artifacts hanging from the walls/ceiling, etc. Finally, it would be beneficial if the business card design elements can be easily used on flyers and other promotional assets. Good luck, we are looking forward to seeing your creative ideas.

Target Market(s)

Coffee lovers and cycling fans

Contact Information for Business Card

See project description.

Colors

Designer to choose colors to be used in the design.

Requirements
Must have
• Must use the current logo provided and combine a coffee and bike theme.
Nice to have
• Orange is used in current logo and could be used as an accent color on the backside of the business card.

```html
<!DOCTYPE html>
<html lang="en">
<head>
<meta charset="utf-8">
<title>KR Coffee House – Business Cards</title>
<link href="https://fonts.googleapis.com/css2?family=Lato:wght@400;700&family=Open+Sans:wght@400&display=swap" rel="stylesheet">
<style>
  :root {
    --backdrop: #333333;
    --card-light: #ececec;
    --charcoal: #3d3d3d;
    --orange: #ff6a1f;
    --white: #ffffff;
  }
  html, body {
    margin: 0;
    padding: 0;
    overflow: hidden;
  }
  body {
    width: 1200px;
    height: 1200px;
    background: var(--backdrop);
    position: relative;
  }
  .card {
    position: absolute;
    top: 310px;
    height: 594px;
    overflow: hidden;
  }

  /* Front card */
  .card-front {
    left: 234px;
    width: 364px;
    background: var(--card-light);
  }
  .front-wordmark {
    position: absolute;
    top: 395px;
    left: 0;
    width: 100%;
    text-align: center;
    font: 700 120px/1 "Lato", sans-serif;
    color: var(--orange);
    letter-spacing: 4px;
  }
  .front-wordmark {
    top: 90px;
  }
  .front-title {
    position: absolute;
    top: 243px;
    left: 0;
    width: 100%;
    text-align: center;
    font: 400 37px/1 "Lato", sans-serif;
    color: var(--charcoal);
    letter-spacing: 0.5px;
  }
  .tagline-band {
    position: absolute;
    top: 365px;
    left: 0;
    width: 100%;
    height: 112px;
    background: var(--charcoal);
    display: flex;
    align-items: center;
    justify-content: center;
  }
  .tagline {
    margin: 0;
    text-align: center;
    font: 700 34px/41px "Lato", sans-serif;
    color: var(--orange);
  }
  .address {
    position: absolute;
    top: 506px;
    left: 0;
    width: 100%;
    text-align: center;
    font: 400 16.5px/22px "Open Sans", sans-serif;
    color: var(--charcoal);
  }

  /* Back card */
  .card-back {
    left: 627px;
    width: 369px;
    background: var(--charcoal);
  }
  .back-top {
    position: absolute;
    top: 0;
    left: 0;
    width: 100%;
    height: 280px;
    background: var(--orange);
  }
  .website {
    position: absolute;
    top: 67px;
    left: 0;
    width: 100%;
    text-align: center;
    font: 400 20px/1 "Open Sans", sans-serif;
    color: var(--white);
    letter-spacing: 0.5px;
  }
  .back-wordmark {
    position: absolute;
    top: 190px;
    left: 0;
    width: 100%;
    text-align: center;
    font: 700 170px/1 "Lato", sans-serif;
    color: var(--white);
    letter-spacing: 6px;
  }
  .social-row {
    position: absolute;
    top: 490px;
    left: 55px;
    width: 259px;
    height: 36px;
    display: flex;
    align-items: center;
    gap: 6px;
  }
  .social-rule {
    flex: 1;
    height: 1px;
    background: rgba(255, 255, 255, 0.7);
  }
  .social-dot {
    width: 35px;
    height: 35px;
    border-radius: 50%;
    background: var(--white);
  }
  .social-handle {
    position: absolute;
    top: 534px;
    left: 0;
    width: 100%;
    text-align: center;
    font: 400 20px/1 "Open Sans", sans-serif;
    color: var(--white);
  }
</style>
</head>
<body>
  <section class="card card-front">
    <div class="front-wordmark">KR</div>
    <div class="front-title">COFFEE HOUSE</div>
    <div class="tagline-band">
      <p class="tagline">YOUR TAGLINE<br>GOES HERE</p>
    </div>
    <div class="address">12345, Address Goes Here<br>Country Name, 123456.</div>
  </section>

  <section class="card card-back">
    <div class="back-top"></div>
    <div class="website">www.krcoffeehouse.com</div>
    <div class="back-wordmark">KR</div>
    <div class="social-row">
      <span class="social-rule"></span>
      <span class="social-dot" role="img" aria-label="Social network link"></span>
      <span class="social-dot" role="img" aria-label="Social network link"></span>
      <span class="social-rule"></span>
    </div>
    <div class="social-handle">krcoffeehouse</div>
  </section>
</body>
</html>
```